Corvane Capital Business Cards

These are professional business cards that are for my family office.
Put fake emails and phone numbers as of now until I finalize those components. This family office controls my families investments, assets, and future. The cards should be professional.
..
.
.
.
I just uploaded another variation of a logo I would like to see as a business card to I am inbeteen which logo to use

Target Market(s)

business

Industry/Entity Type

business

Contact Information for Business Card

Professional, wealth related, finance related.

Requirements
Must have
• Logo

```html
<!DOCTYPE html>
<html lang="en">
<head>
<meta charset="utf-8">
<title>Corvane Capital Business Cards</title>
<link rel="stylesheet" href="https://fonts.googleapis.com/css2?family=Playfair+Display:wght@400&family=Raleway:wght@700&family=Roboto:wght@400&display=swap">
<style>
  :root {
    --backdrop: #d1d2d4;
    --card-front: #f2f2f4;
    --ink: #111111;
    --gold: #c8ae72;
    --text-grey: #555555;
    --card-back-dark: #060606;
    --card-back-mid: #26272a;
    --card-back-light: #77797d;
    --white: #ffffff;
  }
  * { margin: 0; padding: 0; box-sizing: border-box; }
  html, body {
    width: 1200px; height: 1000px; overflow: hidden;
    background: var(--backdrop);
  }
  .canvas { position: relative; width: 1200px; height: 1000px; }

  .card { position: absolute; left: 283px; width: 634px; height: 362px; overflow: hidden; }
  .card-front { top: 127px; background: var(--card-front); }
  .card-back { top: 511px; background: var(--card-back-dark); }

  .brand-decoration {
    position: absolute; left: 345px; top: 0; width: 289px; height: 188px;
    background: linear-gradient(90deg, rgba(200,200,202,0.6) 0%, rgba(228,224,210,0.6) 55%, rgba(242,242,244,0) 100%);
  }

  .brand-square {
    position: absolute; left: 172px; top: 56px; width: 36px; height: 36px;
    background: var(--gold);
  }
  .brand-name {
    position: absolute; left: 59px; top: 112px;
    font-family: "Playfair Display", serif; font-weight: 400;
    font-size: 29px; letter-spacing: 0.3px; color: var(--ink);
    line-height: 36px; white-space: nowrap;
  }

  .person { position: absolute; left: 59px; top: 263px; }
  .person-name {
    font-family: "Raleway", sans-serif; font-weight: 700;
    font-size: 20px; letter-spacing: 0.3px; color: var(--ink); line-height: 26px;
  }
  .person-role {
    font-family: "Roboto", sans-serif; font-size: 16px; color: var(--gold); line-height: 20px;
  }

  .contact {
    position: absolute; left: 380px; top: 201px;
    font-family: "Roboto", sans-serif; font-size: 16px; color: var(--text-grey);
  }
  .address { font-style: normal; }
  .address p { line-height: 20px; }
  .contact-list { list-style: none; margin-top: 13px; }
  .contact-list li { display: flex; align-items: center; line-height: 21px; }
  .contact-list svg { width: 15px; height: 15px; margin-right: 8px; fill: var(--gold); }

  .back-pattern {
    position: absolute; inset: 0;
    background: linear-gradient(125deg, var(--card-back-light) 0%, #4a4b4f 22%, var(--card-back-mid) 50%, #111213 75%, var(--card-back-dark) 100%);
  }
  .back-brand {
    position: absolute; left: 380px; top: 240px;
    display: flex; align-items: center; gap: 10px;
  }
  .back-square { width: 18px; height: 18px; background: var(--gold); }
  .back-name {
    font-family: "Playfair Display", serif; font-weight: 400;
    font-size: 18px; line-height: 22px; color: var(--white); white-space: nowrap;
  }
</style>
</head>
<body>
<main class="canvas">
  <section class="card card-front">
    <div class="brand-decoration" role="img" aria-label="Large faint brand mark decoration"></div>
    <div class="brand-square" aria-hidden="true"></div>
    <h1 class="brand-name">CORVANE CAPITAL</h1>

    <div class="person">
      <h2 class="person-name">DANIEL ASHFORD</h2>
      <p class="person-role">Managing Director</p>
    </div>

    <div class="contact">
      <address class="address">
        <p>480 Marlow Ave Suite</p>
        <p>Larkspur Bay&nbsp; USA</p>
      </address>
      <ul class="contact-list">
        <li>
          <svg viewBox="0 0 16 16" aria-hidden="true"><path d="M2 6c0-2 2.5-3 6-3s6 1 6 3v1h-3V5.5H5V7H2z M4 8h8l2 5H2z"/></svg>
          (555) 210-4XXX
        </li>
        <li>
          <svg viewBox="0 0 16 16" aria-hidden="true"><path d="M1 3h14v1.5L8 9 1 4.5z M1 6.3l7 4.5 7-4.5V13H1z"/></svg>
          info@corvanecapital.com
        </li>
        <li>
          <svg viewBox="0 0 16 16" aria-hidden="true"><circle cx="8" cy="8" r="7"/></svg>
          www.corvanecapital.com
        </li>
      </ul>
    </div>
  </section>

  <section class="card card-back">
    <div class="back-pattern" role="img" aria-label="Embossed repeating brand mark pattern on black stock, glossy silver fading to black"></div>
    <div class="back-brand">
      <span class="back-square" aria-hidden="true"></span>
      <p class="back-name">CORVANE CAPITAL</p>
    </div>
  </section>
</main>
</body>
</html>
```